Upscale business cards needed for Board of Directors

We need professional business cards created for members of our family business Board of Directors. We would like these relatively simple and straightforward, but also with a unique element to set them apart. Probably stick with neutral and simple colors - white, grey etc. We need space for the traditional elements, including name, title, address, email/phone number. And we will be creating several from this template so it needs to be template that is easy to switch information in and out of.
Business
See description

```html
<!DOCTYPE html>
<html lang="en">
<head>
<meta charset="utf-8">
<title>Harbourline Holdings – Business Card</title>
<link rel="stylesheet" href="https://fonts.googleapis.com/css2?family=Source+Sans+3:wght@400;700&display=swap">
<style>
  :root {
    --backdrop: #181818;
    --paper: #ffffff;
    --gold: #b39c72;
    --ink: #1c1c1c;
    --reverse: #ffffff;
  }
  * { margin: 0; padding: 0; box-sizing: border-box; }
  html, body { width: 1200px; height: 900px; overflow: hidden; }
  body {
    background: var(--backdrop);
    font-family: "Source Sans 3", "Myriad Pro", sans-serif;
    position: relative;
  }
  .card {
    position: absolute;
    top: 306px;
    width: 440px;
    height: 271px;
    border-radius: 10px;
  }
  .card--front { left: 149px; background: var(--paper); }
  .card--back { left: 608px; background: var(--gold); }

  .wordmark {
    position: absolute;
    font-weight: 700;
    text-transform: uppercase;
    line-height: 1;
  }
  .wordmark__line1 { display: block; }
  .wordmark__line2 { display: block; }

  .card--front .wordmark {
    left: 27px; top: 38px; width: 226px;
    color: var(--ink); text-align: center;
  }
  .card--front .wordmark__line1 { font-size: 35px; letter-spacing: 0.5px; }
  .card--front .wordmark__line2 { font-size: 19px; letter-spacing: 7px; margin-top: 5px; padding-left: 7px; }

  .card--back .wordmark {
    left: 0; right: 0; top: 110px;
    color: var(--reverse); text-align: center;
  }
  .card--back .wordmark__line1 { font-size: 37px; letter-spacing: 0.5px; }
  .card--back .wordmark__line2 { font-size: 20px; letter-spacing: 7px; margin-top: 5px; padding-left: 7px; }

  .details {
    position: absolute;
    left: 252px; top: 107px;
    color: var(--ink);
    font-size: 12.5px;
    line-height: 16px;
  }
  .details__name { color: var(--gold); font-size: 18.5px; line-height: 22px; }
  .details__title { margin-bottom: 10px; }
  .details__address { margin-bottom: 9px; }
  .contact { list-style: none; }
  .contact__item { display: flex; align-items: center; gap: 6px; }
  .contact__icon { width: 10px; height: 10px; fill: var(--gold); flex: none; }
</style>
</head>
<body>
  <section class="card card--front" aria-label="Card front">
    <div class="wordmark">
      <span class="wordmark__line1">Harbourline</span>
      <span class="wordmark__line2">Holdings</span>
    </div>
    <div class="details">
      <p class="details__name">Daniel Hartley</p>
      <p class="details__title">Managing Director</p>
      <p class="details__address">12345, Address Goes Here<br>Country Name, 123456.</p>
      <ul class="contact">
        <li class="contact__item">
          <svg class="contact__icon" viewBox="0 0 10 10" aria-hidden="true"><path d="M2 0.5l1.6 2-0.9 1.2c0.6 1.3 1.4 2.1 2.6 2.6l1.2-0.9 2 1.6-1 1.9C4.5 8.9 1.1 5.5 0.6 1.5z"/></svg>
          <span>044-987 654 321</span>
        </li>
        <li class="contact__item">
          <svg class="contact__icon" viewBox="0 0 10 10" aria-hidden="true"><path d="M0.5 2h9v6h-9z M0.5 2l4.5 3.5L9.5 2" fill="var(--gold)"/><path d="M1 2.5l4 3 4-3" fill="none" stroke="#fff" stroke-width="0.8"/></svg>
          <span>hello@sitename.com</span>
        </li>
        <li class="contact__item">
          <svg class="contact__icon" viewBox="0 0 10 10" aria-hidden="true"><path d="M4 6l2-2" stroke="var(--gold)" stroke-width="1.2" fill="none"/><path d="M3.5 4.5L2 6a1.4 1.4 0 0 0 2 2l1.5-1.5M6.5 5.5L8 4a1.4 1.4 0 0 0-2-2L4.5 3.5" stroke="var(--gold)" stroke-width="1.2" fill="none"/></svg>
          <span>www.sitename.com</span>
        </li>
      </ul>
    </div>
  </section>

  <section class="card card--back" aria-label="Card back">
    <div class="wordmark">
      <span class="wordmark__line1">Harbourline</span>
      <span class="wordmark__line2">Holdings</span>
    </div>
  </section>
</body>
</html>
```